We would like to obtain a sales orientated brochure to promote our two models of thermal imaging cameras as a response to the current Covid 19 health issues. I have provided the text, photos and detailed product specifications , in addition to a sample competitors brochure.
BROCHURE Details : 2 sided - front side to show product, its applications in business, school, hospitals, with text details - Back page to show specifications chart and contact information for Korvel Display Group. (Melbourne -Sydney-Perth-Brisbane - 1300 618 475
Brochure should be "eye-catching" and reflect the product as a high quality, must-have technology device for todays world.

```html
<!DOCTYPE html>
<html lang="en">
<head>
<meta charset="utf-8">
<title>Korvel Display Group – Thermal Scanning Brochure</title>
<link href="https://fonts.googleapis.com/css2?family=Montserrat:wght@400;500;600;700;800;900&display=swap" rel="stylesheet">
<style>
  :root{
    --bg:#eeeff0;
    --sheet-grey:#d5d7db;
    --navy-deep:#0d0f24;
    --navy:#1a1d45;
    --violet:#2a2768;
    --blue:#2f5fb8;
    --blue-bright:#4c86e0;
    --sky:#7fb0ff;
    --ink:#16171c;
    --white:#ffffff;
    --logo-grey:#8a8d93;
    --band:#0a0a0c;
  }
  *{box-sizing:border-box;margin:0;padding:0}
  html,body{width:1200px;height:1200px;overflow:hidden;background:var(--bg);font-family:"Montserrat",sans-serif}
  .canvas{position:relative;width:1200px;height:1200px}
  .sheet{position:absolute;top:220px;width:540px;height:760px;overflow:hidden;box-shadow:0 2px 8px rgba(0,0,0,.12)}
  .sheet--back{left:40px;background:var(--sheet-grey)}
  .sheet--front{left:620px;background:radial-gradient(ellipse at 50% 100%,#3a2f86 0%,#1b1b48 35%,var(--navy-deep) 75%)}
  .abs{position:absolute}

  /* back */
  .back-curve{position:absolute;inset:0}
  .specs{position:absolute;left:66px;top:64px;width:330px;color:var(--ink)}
  .specs__title{font-weight:800;font-size:11.5px;color:var(--blue);letter-spacing:-.1px;margin-bottom:10px}
  .specs__group{font-weight:800;font-size:8px;color:var(--blue-bright);margin:7px 0 3px}
  .specs__row{display:grid;grid-template-columns:130px 1fr;font-size:6.6px;line-height:8.6px;font-weight:600}
  .specs__row span:last-child{font-weight:500}
  .cta{position:absolute;left:0;top:578px;width:390px;height:88px;background:var(--band)}
  .cta__icon{position:absolute;left:60px;top:12px}
  .cta__line1{position:absolute;left:118px;top:8px;font-weight:900;font-size:24px;color:var(--blue-bright)}
  .cta__line2{position:absolute;left:118px;top:40px;font-weight:800;font-size:11.5px;color:var(--blue)}
  .cta__line3{position:absolute;left:118px;top:54px;font-weight:900;font-size:23px;color:var(--blue-bright)}
  .back-logo{position:absolute;left:66px;top:684px;display:flex;align-items:center;gap:10px}
  .logo-square{width:22px;height:22px;background:var(--blue)}
  .logo-name{font-weight:500;font-size:19px;color:var(--logo-grey)}
  .back-cities{position:absolute;left:74px;top:721px;font-size:9.5px;font-weight:600;color:var(--ink)}
  .back-contact{position:absolute;left:104px;top:739px;font-size:7.5px;font-weight:600;color:var(--ink);display:flex;gap:20px}
  .product{position:absolute;border-radius:6px}
  .caption{position:absolute;color:var(--white);font-weight:800;font-size:10px;line-height:12px;text-align:right}

  /* front */
  .front-logo{position:absolute;left:155px;top:62px;display:flex;align-items:center;gap:12px}
  .front-logo .logo-name{font-size:20px}
  .headline{position:absolute;left:50px;top:118px;width:230px;text-align:right;font-weight:900;color:var(--blue);line-height:.98}
  .headline__small{font-size:26px;display:block}
  .headline__big{font-size:43px;display:block}
  .headline-rule{position:absolute;left:291px;top:122px;width:1px;height:122px;background:var(--blue)}
  .intro{position:absolute;left:304px;top:118px;width:210px;font-size:9px;line-height:12px;color:var(--sky);font-weight:500}
  .col-left{position:absolute;left:58px;top:319px;width:142px;text-align:right;color:var(--sky)}
  .col-right{position:absolute;left:362px;top:352px;width:128px;color:var(--sky)}
  .col-head{font-weight:800;font-size:9px;line-height:11px;margin-bottom:6px}
  .col-text{font-size:6.6px;line-height:8.7px;font-weight:500}
  .col-text + .col-text{margin-top:8px}

  .hero-device{position:absolute;left:147px;top:283px;width:248px;height:405px}
  .hero-device__screen{position:absolute;left:60px;top:0;width:120px;height:265px;border-radius:6px;background:linear-gradient(180deg,#d8dbe2 0%,#3d4257 14%,#1f2336 70%,#2a2e44 100%)}
  .hero-device__pole{position:absolute;left:110px;top:265px;width:20px;height:60px;background:linear-gradient(90deg,#6b6f80,#c4c7d2,#6b6f80)}
  .hero-device__base{position:absolute;left:0;top:320px;width:248px;height:85px;border-radius:14px;background:linear-gradient(180deg,#2b2d3a 0%,#111220 70%,#3a3a80 100%)}
</style>
</head>
<body>
<div class="canvas">

  <!-- BACK PAGE -->
  <section class="sheet sheet--back">
    <svg class="back-curve" width="540" height="760" viewBox="0 0 540 760">
      <defs>
        <linearGradient id="backNight" x1="0" y1="0" x2="1" y2="1">
          <stop offset="0" stop-color="#1c1f4e"/>
          <stop offset=".6" stop-color="#10122e"/>
          <stop offset="1" stop-color="#0b0c22"/>
        </linearGradient>
      </defs>
      <path d="M294 0 C 370 120 400 300 395 430 C 392 560 385 660 370 760 L540 760 L540 0 Z" fill="url(#backNight)"/>
    </svg>

    <div class="specs">
      <h2 class="specs__title">TECHNICAL SPECIFICATIONS</h2>
      <h3 class="specs__group">CAMERA</h3>
      <div class="specs__row"><span>Resolution:</span><span>2 million pixels</span></div>
      <div class="specs__row"><span>Type:</span><span>Binocular wide dynamic camera</span></div>
      <div class="specs__row"><span>Aperture:</span><span>F2.4</span></div>
      <div class="specs__row"><span>Focusing distance:</span><span>50-150cm</span></div>
      <div class="specs__row"><span>White balance:</span><span>auto</span></div>
      <div class="specs__row"><span>Photo flood light:</span><span>LED and IR dual photo flood light</span></div>
      <h3 class="specs__group">SCREEN</h3>
      <div class="specs__row"><span>Size:</span><span>8.0 inch IPS LCD screen</span></div>
      <div class="specs__row"><span>Resolution:</span><span>800×1280</span></div>
      <div class="specs__row"><span>Touch:</span><span>Not supported</span></div>
      <h3 class="specs__group">PROCESSOR</h3>
      <div class="specs__row"><span>CPU:</span><span>KQ-400 quad-core</span></div>
      <div class="specs__row"><span>Storage:</span><span>EMMC 8G</span></div>
      <h3 class="specs__group">INTERFACE</h3>
      <div class="specs__row"><span>Network module:</span><span>Ethernet and wireless (WIFI)</span></div>
      <div class="specs__row"><span>Audio:</span><span>2.5W / 4R speakers</span></div>
      <div class="specs__row"><span>USB:</span><span>1 USB OTG, 1 USB HOST standard A port</span></div>
      <div class="specs__row"><span>Serial communication:</span><span>1 RS232 serial port</span></div>
      <div class="specs__row"><span>Relay output:</span><span>1 door open signal output</span></div>
      <div class="specs__row"><span>Wiegand One Wiegand:</span><span>26/34 output, one Wiegand 26/34 input</span></div>
      <div class="specs__row"><span>Upgrade button:</span><span>Support Uboot upgrade button</span></div>
      <div class="specs__row"><span>Wired network:</span><span>1 RJ45 Ethernet socket</span></div>
      <h3 class="specs__group">FUNCTION</h3>
      <div class="specs__row"><span>Face Detection:</span><span>Supports facial detection</span></div>
      <div class="specs__row"><span>Face library:</span><span>Up to 30,000</span></div>
      <div class="specs__row"><span>1: Nface recognition:</span><span>Support</span></div>
      <div class="specs__row"><span>1: 1face comparison:</span><span>Support</span></div>
      <div class="specs__row"><span>Stranger detection:</span><span>Support</span></div>
      <div class="specs__row"><span>Identify distance configuration:</span><span>Support</span></div>
      <div class="specs__row"><span>UI interface configuration:</span><span>Support</span></div>
      <div class="specs__row"><span>Upgrade remotely:</span><span>Support</span></div>
      <div class="specs__row"><span>Interface:</span><span>Interfaces include device management, personnel / photo management, record query, etc.</span></div>
      <div class="specs__row"><span>Deployment method:</span><span>Support public cloud deployment, privatized deployment, LAN use, stand-alone use</span></div>
      <h3 class="specs__group">INFRARED IMAGING THERMAL MODULE</h3>
      <div class="specs__row"><span>Temperature detection:</span><span>Support</span></div>
      <div class="specs__row"><span>Temperature detection distance:</span><span>1 meter (optimal distance 0.5 meter)</span></div>
      <div class="specs__row"><span>Temperature:</span><span>± 0.5 measurement accuracy</span></div>
      <div class="specs__row"><span>Temperature measurement range:</span><span>10–42</span></div>
      <div class="specs__row"><span>Pixels:</span><span>32 X 32 dots (total 1024 pixels)</span></div>
      <div class="specs__row"><span>Visitors' temperature is normal and released directly:</span><span>Support</span></div>
      <div class="specs__row"><span>Abnormal temperature alarm:</span><span>Support (temperature alarm value can be set)</span></div>
    </div>

    <div class="cta">
      <svg class="cta__icon" width="44" height="44" viewBox="0 0 44 44" fill="none" stroke="#4c86e0" stroke-width="2.5" stroke-linecap="round" stroke-linejoin="round">
        <path d="M10 6 L16 6 L19 14 L15 17 C17 22 22 27 27 29 L30 25 L38 28 L38 34 C38 36 36 38 34 38 C19 37 7 25 6 10 C6 8 8 6 10 6 Z"/>
        <path d="M26 6 C32 7 37 12 38 18"/>
        <path d="M25 12 C28 13 31 15 32 19"/>
      </svg>
      <div class="cta__line1">CALL 1300 618 475</div>
      <div class="cta__line2">FOR FURTHER INFORMATION AND</div>
      <div class="cta__line3">A FREE QUOTE</div>
    </div>

    <div class="back-logo">
      <span class="logo-square"></span>
      <span class="logo-name">Korvel Display Group</span>
    </div>
    <div class="back-cities">MELBOURNE – SYDNEY – PERTH – BRISBANE</div>
    <div class="back-contact"><span>✆ 1300 618 475</span><span>● www.korveldisplay.com.au</span></div>

    <div class="product" role="img" aria-label="Product photo: desk-mounted thermal scanning camera on a triangular base" style="left:398px;top:58px;width:98px;height:210px;background:linear-gradient(180deg,#2c2f48,#111224 70%,#1e2150)"></div>
    <div class="caption" style="right:46px;top:276px">Portable<br>Camera for a<br>Reception Desk</div>
    <div class="product" role="img" aria-label="Product photo: floor-standing thermal scanning camera on a silver pole" style="left:434px;top:345px;width:52px;height:352px;background:linear-gradient(180deg,#2a2d46,#8c8f9c 45%,#5a5d6c 90%,#1b1d35)"></div>
    <div class="caption" style="right:46px;top:706px">Portable Floor<br>Standing Camera</div>
  </section>

  <!-- FRONT PAGE -->
  <section class="sheet sheet--front">
    <div class="front-logo">
      <span class="logo-square"></span>
      <span class="logo-name">Korvel Display Group</span>
    </div>

    <h1 class="headline">
      <span class="headline__small">THERMAL</span>
      <span class="headline__small">SCANNING</span>
      <span class="headline__small">&amp; FACIAL</span>
      <span class="headline__small">RECOGNITION</span>
      <span class="headline__big">CAMERA</span>
    </h1>
    <div class="headline-rule"></div>
    <p class="intro">The temperature of your body is no longer considered private information. That's the stance that businesses around the world are taking as they install thermal imaging cameras for the safety of staff and visitors, often equipped with facial recognition technology, in their buildings in an attempt to cope with the COVID-19 pandemic. It's a movement one might call the automation of temperature checks.</p>

    <svg class="abs" style="left:130px;top:270px" width="300" height="70" viewBox="0 0 300 70" fill="none" stroke="#c9ccd8" stroke-width="1">
      <path d="M140 20 C100 8 60 12 8 30"/><path d="M8 30 l7 -6 M8 30 l9 1"/>
      <path d="M195 22 C225 12 240 35 246 62"/><path d="M246 62 l-1 -9 M246 62 l-6 -6"/>
    </svg>

    <div class="col-left">
      <h3 class="col-head">THE PURPOSE OF<br>THERMAL SCANNING &amp;<br>FACIAL RECOGNITION</h3>
      <p class="col-text">The purpose is to identify anyone walking into an establishment with a high temperature. This will reduce the likelihood of spreading any potential virus and brings some peace of mind to people in the building. We can pair your thermal camera/s with facial recognition software. Employees will check in by standing in front of the camera, which identifies them by their face in just a few seconds without contact (with or without a mask on) and simultaneously performs a thermal scan. It will record a photo of the individual, the date, the time and the temperature reading at that time of entering the building. If the camera detects a high temperature reading, it will sound an alarm in real time and send a notification to a nominated administrator/ in-house security.</p>
    </div>

    <div class="col-right">
      <h3 class="col-head">WHERE AND HOW CAN<br>IT BE USED?</h3>
      <p class="col-text">This Camera can be used with access control gates. It is used in office buildings, schools, hotels, hospitality, in fact, any space where Covid is potentially a threat to staff or visitors.</p>
      <p class="col-text">Our Thermal Scanning &amp; Facial Recognition Camera is used as a safety and security measure.<br>If someone gets sick and takes legal action, you can demonstrate that you have made your best effort to protect your staff and visitors.</p>
    </div>

    <div class="hero-device" role="img" aria-label="Product photo: thermal scanning camera with screen showing an admittance result, on a triangular desk base">
      <div class="hero-device__screen"></div>
      <div class="hero-device__pole"></div>
      <div class="hero-device__base"></div>
    </div>
  </section>

</div>
</body>
</html>
```